7K packaging design

We are a wholesaler for Automotive Spare Parts in Jordan and Iraq market and we needs to import spare parts from China under our company private brand "7K"
The 7K brand’s product lines include Filtration, Braking Systems, Wheels, Wheel Bolts & Nuts, Shock Absorbers, Sensors, Cooling Systems, Axles and more.
The aim of the project is to unify the brand packaging across all the product lines , we will start by the brake pads then based on the approved design we will do the other products

Target Market(s)

Jordan , Iraq Market

Industry/Entity Type

Automotive spare parts

Requirements
Must have
• Name of the product :Ceramic brake pads specs : Superior stopping power Noise suppression Low Dust Technology Made in china
Nice to have
• Brake pad outline image on the box
Should not have
• Blue color

```html
<!DOCTYPE html>
<html lang="en">
<head>
<meta charset="utf-8">
<title>7K packaging design – Ceramic Brake Pads dieline</title>
<link rel="stylesheet" href="https://fonts.googleapis.com/css2?family=Audiowide&family=Montserrat:wght@500;600&display=swap">
<style>
  :root {
    --canvas: #ffffff;
    --dieline: #29abe2;
    --flap-dark: #333333;
    --red: #ff0008;
    --red-mid: #c40005;
    --red-deep: #6a0003;
    --photo-dark: #2f2f2f;
    --photo-light: #8c8c8c;
    --silver-a: #6f6f6f;
    --silver-b: #e6e6e6;
    --band-a: #5a5a5a;
    --band-b: #a3a3a3;
    --white: #ffffff;
    --logo-grey: #a8a8a8;
  }
  * { box-sizing: border-box; margin: 0; padding: 0; }
  html, body { width: 1091px; height: 1200px; overflow: hidden; background: var(--canvas); }
  .dieline-sheet { position: relative; width: 1091px; height: 1200px; }
  .panel { position: absolute; border: 0.6px solid var(--dieline); overflow: hidden; }

  .flap-dark { background: var(--flap-dark); }
  .lid-top { background: linear-gradient(180deg, var(--red-deep) 0%, var(--red-mid) 45%, var(--red) 100%); }
  .lid-back { background: linear-gradient(160deg, var(--red-deep) 0%, var(--red-mid) 35%, var(--red) 75%); }
  .side-red { background: linear-gradient(170deg, var(--red) 0%, var(--red) 35%, var(--red-mid) 75%, var(--red-deep) 100%); }
  .front-face { background: linear-gradient(175deg, var(--red) 0%, var(--red) 55%, var(--red-mid) 85%, var(--red-deep) 100%); }

  .lock-slot { position: absolute; border: 0.6px solid var(--dieline); border-bottom: none; height: 14px; }
  .tuck-tab { position: absolute; background: var(--red-deep); border: 0.6px solid var(--dieline); border-top: none; height: 9px; }

  .car-photo {
    position: absolute; inset: 0;
    background: linear-gradient(200deg, var(--photo-dark) 0%, #555 45%, var(--photo-light) 100%);
  }

  /* brand mark */
  .brand { position: absolute; display: flex; align-items: center; gap: 6px; }
  .brand-dot { border-radius: 50%; background: var(--logo-grey); }
  .brand-name { font-family: "Audiowide", sans-serif; color: var(--white); line-height: 1; }

  .product-name { position: absolute; font-family: "Audiowide", sans-serif; color: var(--white); line-height: 1; white-space: nowrap; }

  /* feature row */
  .features { position: absolute; display: flex; align-items: center; }
  .feature { display: flex; align-items: center; gap: 5px; }
  .feature svg { flex: none; }
  .feature-label { font-family: "Montserrat", sans-serif; font-weight: 600; color: var(--white); font-size: 5.6px; line-height: 1.15; text-transform: uppercase; }

  .pad-outline {
    position: absolute; border-radius: 40% 30% 45% 35%;
    background: radial-gradient(ellipse at center, rgba(255,255,255,0.10), rgba(255,255,255,0) 70%);
  }

  /* the large front/back face used twice (once upside down) */
  .hero-face { background: linear-gradient(90deg, var(--band-a), var(--band-b)); }
  .hero-face .photo-zone { position: absolute; inset: 0; clip-path: polygon(0 0, 258px 0, 151px 100%, 0 100%); }
  .hero-face .silver-stripe { position: absolute; inset: 0; background: linear-gradient(90deg, var(--silver-a), var(--silver-b), var(--silver-a)); clip-path: polygon(258px 0, 272px 0, 165px 100%, 151px 100%); }
  .hero-face .red-zone { position: absolute; inset: 0; background: linear-gradient(180deg, var(--red) 0%, var(--red-mid) 60%, var(--red-deep) 100%); clip-path: polygon(272px 0, 100% 0, 100% 164px, 185px 164px); }
  .upside-down { transform: rotate(180deg); }

  .origin { position: absolute; font-family: "Montserrat", sans-serif; font-weight: 600; color: var(--white); font-size: 8px; letter-spacing: 0.2px; }

  .flaps-and-lines { position: absolute; inset: 0; pointer-events: none; }
</style>
</head>
<body>
<main class="dieline-sheet">

  <svg class="flaps-and-lines" width="1091" height="1200" viewBox="0 0 1091 1200" aria-hidden="true">
    <defs>
      <linearGradient id="dust-flap-left" x1="1" y1="0" x2="0" y2="1">
        <stop offset="0" stop-color="#ff0008"/>
        <stop offset="0.5" stop-color="#ff0008"/>
        <stop offset="1" stop-color="#7a0004"/>
      </linearGradient>
      <linearGradient id="dust-flap-right" x1="0" y1="0" x2="1" y2="1">
        <stop offset="0" stop-color="#ff0008"/>
        <stop offset="0.5" stop-color="#ff0008"/>
        <stop offset="1" stop-color="#7a0004"/>
      </linearGradient>
    </defs>
    <path d="M296,937 L152,937 C128,937 117,956 117,992 C117,1035 150,1092 190,1120 C206,1132 222,1136 242,1136 L296,1139 Z"
          fill="url(#dust-flap-left)" stroke="#29abe2" stroke-width="0.6"/>
    <path d="M796,937 L940,937 C964,937 975,956 975,992 C975,1035 942,1092 902,1120 C886,1132 870,1136 850,1136 L796,1139 Z"
          fill="url(#dust-flap-right)" stroke="#29abe2" stroke-width="0.6"/>
  </svg>

  <!-- row 1: lid tuck flap and dust flaps -->
  <div class="panel flap-dark" style="left:60px;top:61px;width:236px;height:202px;"></div>
  <div class="panel lid-top" style="left:296px;top:61px;width:500px;height:202px;"></div>
  <div class="panel flap-dark" style="left:796px;top:61px;width:236px;height:202px;"></div>

  <!-- row 2: lid -->
  <div class="panel flap-dark" style="left:60px;top:297px;width:236px;height:201px;">
    <div class="lock-slot" style="left:76px;top:187px;width:84px;"></div>
  </div>
  <div class="panel lid-back" style="left:296px;top:263px;width:500px;height:235px;"></div>
  <div class="panel flap-dark" style="left:796px;top:297px;width:236px;height:201px;">
    <div class="lock-slot" style="left:75px;top:187px;width:85px;"></div>
  </div>

  <!-- row 3: back wall (upside down) and side walls -->
  <div class="panel" style="left:60px;top:498px;width:236px;height:203px;">
    <div class="car-photo" role="img" aria-label="Black and white photo of a sports car front wheel"></div>
  </div>

  <div class="panel hero-face upside-down" style="left:296px;top:498px;width:500px;height:203px;">
    <div class="photo-zone"><div class="car-photo" role="img" aria-label="Black and white photo of a sports car"></div></div>
    <div class="silver-stripe"></div>
    <div class="red-zone">
      <div class="pad-outline" role="img" aria-label="White outline drawing of a pair of brake pads" style="left:270px;top:14px;width:210px;height:148px;"></div>
    </div>
    <div class="brand" style="left:14px;top:16px;">
      <span class="brand-dot" style="width:14px;height:14px;"></span>
      <span class="brand-name" style="font-size:32px;">7K</span>
    </div>
    <div class="product-name" style="left:16px;top:116px;font-size:19px;line-height:0.98;">Ceramic<br>Brake<br>Pads</div>
    <div class="features" style="left:220px;top:171px;gap:15px;">
      <div class="feature">
        <svg width="24" height="24" viewBox="0 0 24 24"><circle cx="12" cy="12" r="11" fill="#fff"/><circle cx="12" cy="12" r="6" fill="none" stroke="#777" stroke-width="1"/><circle cx="12" cy="12" r="2" fill="#777"/></svg>
        <span class="feature-label">Superior<br>Stopping<br>Power</span>
      </div>
      <div class="feature">
        <svg width="20" height="20" viewBox="0 0 20 20" fill="none" stroke="#fff" stroke-width="1.3"><path d="M2 7h4l5-4v14l-5-4H2z"/><path d="M14 5l4-2M14 10h4M14 15l4 2"/></svg>
        <span class="feature-label">Noise<br>Suppression</span>
      </div>
      <div class="feature">
        <svg width="20" height="20" viewBox="0 0 20 20" fill="none" stroke="#fff" stroke-width="1.1" stroke-dasharray="2 1.5"><circle cx="10" cy="10" r="8"/><circle cx="8" cy="9" r="3"/></svg>
        <span class="feature-label">Low Dust<br>Technology</span>
      </div>
    </div>
  </div>

  <div class="panel" style="left:796px;top:498px;width:236px;height:203px;">
    <div class="upside-down" style="position:absolute;inset:0;">
      <div class="car-photo" role="img" aria-label="Black and white photo of a sports car front wheel"></div>
      <div class="brand" style="left:62px;top:26px;">
        <span class="brand-dot" style="width:16px;height:16px;"></span>
        <span class="brand-name" style="font-size:40px;">7K</span>
      </div>
      <div class="product-name" style="left:28px;top:150px;font-size:13px;">Ceramic Brake Pads</div>
      <div class="origin" style="left:84px;top:176px;">MADE IN CHINA</div>
    </div>
  </div>

  <!-- row 4: base front and side walls -->
  <div class="panel side-red" style="left:60px;top:701px;width:236px;height:193px;"></div>
  <div class="tuck-tab" style="left:132px;top:894px;width:92px;"></div>

  <div class="panel front-face" style="left:296px;top:701px;width:500px;height:236px;">
    <div class="pad-outline" role="img" aria-label="White outline drawing of a pair of brake pads" style="left:225px;top:37px;width:253px;height:162px;"></div>
    <div class="brand" style="left:22px;top:28px;">
      <span class="brand-dot" style="width:16px;height:16px;"></span>
      <span class="brand-name" style="font-size:44px;">7K</span>
    </div>
    <div class="product-name" style="left:23px;top:130px;font-size:17.5px;">Ceramic Brake Pads</div>
    <div class="features" style="left:22px;top:181px;gap:14px;">
      <div class="feature">
        <svg width="22" height="22" viewBox="0 0 24 24"><circle cx="12" cy="12" r="11" fill="#fff"/><circle cx="12" cy="12" r="6" fill="none" stroke="#d00" stroke-width="1"/><circle cx="12" cy="12" r="2" fill="#d00"/></svg>
        <span class="feature-label">Superior<br>Stopping<br>Power</span>
      </div>
      <div class="feature">
        <svg width="18" height="18" viewBox="0 0 20 20" fill="none" stroke="#fff" stroke-width="1.3"><path d="M2 7h4l5-4v14l-5-4H2z"/><path d="M14 5l4-2M14 10h4M14 15l4 2"/></svg>
        <span class="feature-label">Noise<br>Suppression</span>
      </div>
      <div class="feature">
        <svg width="18" height="18" viewBox="0 0 20 20" fill="none" stroke="#fff" stroke-width="1.1" stroke-dasharray="2 1.5"><circle cx="10" cy="10" r="8"/><circle cx="8" cy="9" r="3"/></svg>
        <span class="feature-label">Low Dust<br>Technology</span>
      </div>
    </div>
  </div>

  <div class="panel side-red" style="left:796px;top:701px;width:236px;height:193px;"></div>
  <div class="tuck-tab" style="left:868px;top:894px;width:92px;"></div>

  <!-- row 5: base back face -->
  <div class="panel hero-face" style="left:296px;top:937px;width:500px;height:202px;">
    <div class="photo-zone"><div class="car-photo" role="img" aria-label="Black and white photo of a sports car"></div></div>
    <div class="silver-stripe"></div>
    <div class="red-zone">
      <div class="pad-outline" role="img" aria-label="White outline drawing of a pair of brake pads" style="left:265px;top:14px;width:215px;height:148px;"></div>
    </div>
    <div class="brand" style="left:14px;top:16px;">
      <span class="brand-dot" style="width:14px;height:14px;"></span>
      <span class="brand-name" style="font-size:32px;">7K</span>
    </div>
    <div class="product-name" style="left:16px;top:116px;font-size:19px;line-height:0.98;">Ceramic<br>Brake<br>Pads</div>
    <div class="features" style="left:220px;top:171px;gap:15px;">
      <div class="feature">
        <svg width="24" height="24" viewBox="0 0 24 24"><circle cx="12" cy="12" r="11" fill="#fff"/><circle cx="12" cy="12" r="6" fill="none" stroke="#777" stroke-width="1"/><circle cx="12" cy="12" r="2" fill="#777"/></svg>
        <span class="feature-label">Superior<br>Stopping<br>Power</span>
      </div>
      <div class="feature">
        <svg width="20" height="20" viewBox="0 0 20 20" fill="none" stroke="#fff" stroke-width="1.3"><path d="M2 7h4l5-4v14l-5-4H2z"/><path d="M14 5l4-2M14 10h4M14 15l4 2"/></svg>
        <span class="feature-label">Noise<br>Suppression</span>
      </div>
      <div class="feature">
        <svg width="20" height="20" viewBox="0 0 20 20" fill="none" stroke="#fff" stroke-width="1.1" stroke-dasharray="2 1.5"><circle cx="10" cy="10" r="8"/><circle cx="8" cy="9" r="3"/></svg>
        <span class="feature-label">Low Dust<br>Technology</span>
      </div>
    </div>
  </div>

</main>
</body>
</html>
```